Brightway Haus Inc. Business Card Design

Brightway Haus Inc. is in search of a great clean design for our business cards!

Looking to incorporate our full logo and watermark on side one (however, I am open to having the text and watermark separated within the design.)

On side two, I am looking to have contact information (Name, Position, Phone #, Email, Website (www.thebrightwayhaus.ca). Can have the logo and/or watermark as part of the design if applicable.

Please add tagline "Where Shine Counts" on either side 1 or 2. This tagline can be in a sans serif, serif or cursive font as long as it compliments overall design. Capitalization can be title or sentence case depending on how it fits within the design.

Get creative!! Looking for a clean, crisp, premium design! Looking for a glossy card finish with spot UV features when printed. Cards will also be printed with rounded corners. Standard dimensions (3.5 x 2).

Target Market(s)

B2B - primary clients are business owners or property management corporations. (residential jobs are few and far between)

Industry/Entity Type

Business

Contact Information for Business Card

- clean, crisp design
- double sided
- spot UV accents and glossy finish upon printing
- standard business card size (3.5 x 2) with rounded corners
- please see project description for requirements per side

Font styles to use
Sans Serif

Requirements
Must have
• - adequate bleeds with print ready files
• - cohesive design elements between side 1 & 2
• - spot UV elements (can be on both sides or just one, use your discretion)
• - colour pallet should match the logo file provided
• - incorporate tagline "where shine counts" (this tagline can be in a serif or sans serif font as long as it is complimentary to the overall design.
Nice to have
• - Premium elements with a clean design
Should not have
• - Please omit cartoon or whimsical like designs, think premium.
• - Colours should not stray from the pallet of the provided logo.

```html
<!DOCTYPE html>
<html lang="en">
<head>
<meta charset="utf-8">
<title>Brightway Haus Inc. Business Card</title>
<link rel="stylesheet" href="https://fonts.googleapis.com/css2?family=Open+Sans:wght@700&family=Roboto:wght@400;500;700&display=swap">
<style>
  :root {
    --teal: #119ea3;
    --teal-deep: #0a9398;
    --teal-light: #1aa9ae;
    --navy: #1c1f45;
    --card-white: #f4f4f4;
    --card-grey: #e4e4e4;
    --backdrop: #ebebeb;
  }
  * { margin: 0; padding: 0; box-sizing: border-box; }
  html, body { width: 1200px; height: 576px; overflow: hidden; }
  body {
    position: relative;
    background: var(--backdrop);
    font-family: "Roboto", Arial, sans-serif;
    color: var(--navy);
  }
  .card {
    position: absolute;
    top: 138px;
    height: 293px;
    border-radius: 14px;
    overflow: hidden;
    box-shadow: 0 3px 6px rgba(0,0,0,0.18);
  }
  .card-front {
    left: 82px;
    width: 484px;
    background: linear-gradient(160deg, var(--teal-light) 0%, var(--teal) 55%, var(--teal-deep) 100%);
  }
  .card-back {
    left: 602px;
    width: 481px;
    background: linear-gradient(135deg, var(--card-white) 0%, #efefef 55%, var(--card-grey) 100%);
  }
  .brand-front {
    position: absolute;
    left: 0; right: 0; top: 124px;
    display: flex; align-items: center; justify-content: center; gap: 12px;
  }
  .brand-front .brand-mark {
    width: 30px; height: 30px; background: #ffffff;
  }
  .brand-front .brand-name {
    font-family: "Open Sans", Arial, sans-serif;
    font-weight: 700;
    font-size: 34px;
    color: #ffffff;
    letter-spacing: -0.5px;
  }
  .brand-back {
    position: absolute;
    left: 20px; width: 230px; top: 86px;
    display: flex; flex-direction: column; align-items: center;
  }
  .brand-back .brand-mark {
    width: 58px; height: 58px; background: var(--teal);
    margin-bottom: 20px;
  }
  .brand-back .brand-name {
    font-family: "Open Sans", Arial, sans-serif;
    font-weight: 700;
    font-size: 22px;
    color: var(--teal);
    white-space: nowrap;
  }
  .tagline {
    margin-top: 4px;
    font-size: 11px;
    letter-spacing: 2.4px;
    color: var(--navy);
    white-space: nowrap;
  }
  .contact {
    position: absolute;
    left: 282px; top: 68px;
  }
  .contact-name {
    font-size: 20px; font-weight: 700; color: var(--teal);
    line-height: 1.1;
  }
  .contact-role { font-size: 12px; margin-top: 3px; }
  .contact-address { font-size: 12.5px; line-height: 16px; margin-top: 24px; }
  .contact-list { list-style: none; margin-top: 4px; }
  .contact-list li {
    display: flex; align-items: center; gap: 9px;
    font-size: 12.5px; line-height: 18px;
  }
  .contact-list svg { width: 10px; height: 10px; fill: var(--teal); flex: none; }
  .contact-list .accent { color: var(--teal); }
</style>
</head>
<body>
  <section class="card card-front" aria-label="Card front">
    <div class="brand-front">
      <span class="brand-mark"></span>
      <span class="brand-name">Brightway Haus Inc.</span>
    </div>
  </section>

  <section class="card card-back" aria-label="Card back">
    <div class="brand-back">
      <span class="brand-mark"></span>
      <span class="brand-name">Brightway Haus Inc.</span>
      <span class="tagline">Where Shine Counts</span>
    </div>

    <div class="contact">
      <p class="contact-name">Daniel Mercer</p>
      <p class="contact-role">Managing Director</p>
      <p class="contact-address">48 Harbour Lane<br>Unit 2, Canada A1B 2C3</p>
      <ul class="contact-list">
        <li>
          <svg viewBox="0 0 10 10" aria-hidden="true"><path d="M1 3.2C1 2 2.5 1.3 5 1.3S9 2 9 3.2v.8H7V3.2H3V4H1zM2.3 4.6h5.4L9 8.7H1z"/></svg>
          1800-555-0142
        </li>
        <li>
          <svg viewBox="0 0 10 10" aria-hidden="true"><path d="M0.5 2h9v0.6L5 5.6 0.5 2.6zM0.5 3.6 5 6.6l4.5-3V8.2h-9z"/></svg>
          dmercer@brightwayhaus.ca
        </li>
        <li>
          <svg viewBox="0 0 10 10" aria-hidden="true"><path d="M5 0.5a4.5 4.5 0 1 0 0 9 4.5 4.5 0 0 0 0-9zm0 1c.7.7 1.1 1.8 1.2 3H3.8C3.9 3.3 4.3 2.2 5 1.5zM1.5 5.5h1.3c.1 1 .4 1.9.8 2.6A3.5 3.5 0 0 1 1.5 5.5zm0-1a3.5 3.5 0 0 1 2.1-2.6c-.4.7-.7 1.6-.8 2.6zm2.3 1h2.4c-.1 1.2-.5 2.3-1.2 3-.7-.7-1.1-1.8-1.2-3zm2.6 2.6c.4-.7.7-1.6.8-2.6h1.3a3.5 3.5 0 0 1-2.1 2.6zm.8-3.6c-.1-1-.4-1.9-.8-2.6a3.5 3.5 0 0 1 2.1 2.6z"/></svg>
          <span>www.<span class="accent">thebrightwayhaus</span>.ca</span>
        </li>
      </ul>
    </div>
  </section>
</body>
</html>
```